Hollow Mesa Farm Vault Reserve Wine Label (Front and Back)

I need to create an elite tier wine label.  I would like it to be in a light, natural color with silver or gold.  I would like it to look rich and expensive, mostly monochromatic, elegantly simple.  It will need to stand up next to wine labels that are black and charcoal colored and look like the more expensive wine of the 3.  I have attached a similar label that it will be grouped with and some instructions.
We are a winery in southeast Washington state with a reputation for fine wines and top notch terroir.  We want to present family, tradition and high value wine in the bottle.

```html
<!DOCTYPE html>
<html lang="en">
<head>
<meta charset="utf-8">
<title>Hollow Mesa Farm – Vault Reserve Cabernet Sauvignon Label</title>
<link rel="stylesheet" href="https://fonts.googleapis.com/css2?family=Marcellus&family=Italiana&family=Open+Sans:wght@700&display=swap">
<style>
  :root {
    --backdrop: #e3e6e5;
    --wine: #771718;
    --wine-soft: #85282a;
    --cream: #d5d3ca;
    --cream-band: #e2dcd1;
    --cream-text: #e8e1d6;
    --gold-dark: #8c5a35;
    --gold-mid: #c99a62;
    --gold-light: #f0d692;
  }
  * { margin: 0; padding: 0; box-sizing: border-box; }
  html, body {
    width: 1000px;
    height: 1200px;
    overflow: hidden;
    background: var(--backdrop);
  }
  .label {
    position: absolute;
    left: 246px;
    top: 222px;
    width: 509px;
    height: 775px;
  }
  .label-art {
    position: absolute;
    inset: 0;
    display: block;
  }
  .line {
    position: absolute;
    left: 0;
    right: 0;
    text-align: center;
    line-height: 1;
    white-space: nowrap;
  }
  .brand-mark {
    top: 161px;
    display: flex;
    justify-content: center;
    align-items: center;
    gap: 5px;
    font-family: "Marcellus", serif;
    font-size: 11px;
    letter-spacing: 1px;
    color: var(--wine);
    text-transform: uppercase;
  }
  .brand-mark .dot {
    width: 7px;
    height: 7px;
    background: var(--wine);
  }
  .name-primary {
    top: 224px;
    font-family: "Marcellus", serif;
    font-size: 64px;
    color: var(--wine);
    letter-spacing: 1px;
  }
  .name-secondary {
    top: 287px;
    font-family: "Marcellus", serif;
    font-size: 27px;
    color: var(--wine);
    letter-spacing: 1px;
  }
  .region {
    top: 344px;
    font-family: "Open Sans", sans-serif;
    font-weight: 700;
    font-size: 16px;
    letter-spacing: 2px;
    color: var(--wine);
  }
  .vineyard {
    top: 400px;
    font-family: "Open Sans", sans-serif;
    font-weight: 700;
    font-size: 16px;
    letter-spacing: 2px;
    color: var(--cream-text);
  }
  .vintage {
    top: 430px;
    font-family: "Italiana", serif;
    font-size: 23px;
    letter-spacing: 2px;
    color: var(--cream-text);
  }
  .tier {
    top: 549px;
    height: 46px;
    display: flex;
    align-items: center;
    justify-content: center;
    font-family: "Italiana", serif;
    font-size: 24px;
    letter-spacing: 1px;
    color: var(--cream-text);
  }
  .varietal {
    top: 614px;
    font-family: "Italiana", serif;
    font-size: 30px;
    color: var(--wine);
  }
  .heritage {
    top: 699px;
    font-family: "Italiana", serif;
    font-size: 13.5px;
    color: var(--cream-text);
  }
  .heritage .count {
    font-size: 22px;
    vertical-align: -3px;
    padding: 0 6px;
  }
</style>
</head>
<body>
  <main class="label">
    <svg class="label-art" width="509" height="775" viewBox="0 0 509 775" aria-hidden="false">
      <defs>
        <linearGradient id="gold-frame" x1="0" y1="0" x2="1" y2="1">
          <stop offset="0" stop-color="#c99a62"/>
          <stop offset="0.25" stop-color="#f0d692"/>
          <stop offset="0.5" stop-color="#9a6238"/>
          <stop offset="0.75" stop-color="#d8b07a"/>
          <stop offset="1" stop-color="#8c5a35"/>
        </linearGradient>
        <linearGradient id="gold-strip" x1="0" y1="0" x2="1" y2="0">
          <stop offset="0" stop-color="#a97a4c"/>
          <stop offset="0.3" stop-color="#f0d692"/>
          <stop offset="0.55" stop-color="#8c5a35"/>
          <stop offset="0.85" stop-color="#d8b07a"/>
          <stop offset="1" stop-color="#b5865a"/>
        </linearGradient>
        <linearGradient id="gold-rule" x1="0" y1="0" x2="1" y2="0">
          <stop offset="0" stop-color="#c99a62" stop-opacity="0.3"/>
          <stop offset="0.5" stop-color="#9a6238"/>
          <stop offset="1" stop-color="#c99a62" stop-opacity="0.3"/>
        </linearGradient>
        <clipPath id="shield-inner">
          <path transform="translate(254 287) scale(0.92 0.93) translate(-254 -287)"
                d="M254,51 C230,75 200,100 157,108 C130,112 110,112 97,121 C78,135 70,160 77,178 C82,195 85,205 80,220 C70,245 66,270 67,292 C68,330 78,360 83,378 C75,395 72,405 77,418 C85,450 105,464 125,464 L165,464 C185,495 225,505 254,524 C283,505 323,495 343,464 L383,464 C403,464 423,450 431,418 C436,405 433,395 425,378 C430,360 440,330 441,292 C442,270 438,245 428,220 C423,205 426,195 431,178 C438,160 430,135 411,121 C398,112 378,112 351,108 C308,100 278,75 254,51 Z"/>
        </clipPath>
      </defs>

      <rect class="damask-wine" x="0" y="0" width="509" height="376" fill="#7a1a1b"
            role="img" aria-label="Deep red damask pattern background"/>
      <rect class="damask-cream" x="0" y="376" width="509" height="173" fill="#e0d9cd"
            role="img" aria-label="Pale cream damask pattern background"/>
      <rect class="tier-band" x="0" y="549" width="509" height="46" fill="var(--wine)"/>
      <rect class="damask-cream" x="0" y="595" width="509" height="60" fill="#d9d4c9"
            role="img" aria-label="Pale cream damask pattern behind varietal"/>
      <rect class="footer-band" x="0" y="655" width="509" height="120" fill="var(--wine)"/>
      <rect class="gold-strip" x="0" y="668" width="509" height="10" fill="url(#gold-strip)"/>
      <rect class="gold-strip" x="0" y="731" width="509" height="21" fill="url(#gold-strip)"/>

      <path class="shield-frame" fill="url(#gold-frame)"
            d="M254,51 C230,75 200,100 157,108 C130,112 110,112 97,121 C78,135 70,160 77,178 C82,195 85,205 80,220 C70,245 66,270 67,292 C68,330 78,360 83,378 C75,395 72,405 77,418 C85,450 105,464 125,464 L165,464 C185,495 225,505 254,524 C283,505 323,495 343,464 L383,464 C403,464 423,450 431,418 C436,405 433,395 425,378 C430,360 440,330 441,292 C442,270 438,245 428,220 C423,205 426,195 431,178 C438,160 430,135 411,121 C398,112 378,112 351,108 C308,100 278,75 254,51 Z"/>
      <g clip-path="url(#shield-inner)">
        <rect class="shield-field" x="0" y="0" width="509" height="376" fill="var(--cream)"/>
        <rect class="shield-base" x="0" y="376" width="509" height="200" fill="var(--wine)"/>
      </g>

      <rect class="ornament-left" x="148" y="156" width="75" height="28" rx="3" fill="url(#gold-rule)"
            role="img" aria-label="Gold ornamental flourish"/>
      <rect class="ornament-right" x="286" y="156" width="75" height="28" rx="3" fill="url(#gold-rule)"
            role="img" aria-label="Gold ornamental flourish"/>
      <rect class="gold-rule" x="157" y="325" width="194" height="3" rx="1.5" fill="url(#gold-rule)"/>
    </svg>

    <div class="line brand-mark"><span class="dot"></span><span>Hollow Mesa Farm</span></div>
    <h1 class="line name-primary">HOLLOW</h1>
    <p class="line name-secondary">MESA FARM</p>
    <p class="line region">HORSE HEAVEN HILLS</p>
    <p class="line vineyard">ESTATE VINEYARD</p>
    <p class="line vintage">2022</p>
    <p class="line tier">VAULT RESERVE</p>
    <h2 class="line varietal">CABERNET SAUVIGNON</h2>
    <p class="line heritage">FAMILY STEWARDS OF THE LAND FOR<span class="count">5</span>GENERATIONS</p>
  </main>
</body>
</html>
```